Menu Design for coffee shop/cafe

We need a menu designed for our cafe/coffee shop. We want to go for a pretty floral/rustic look, white washed, dusty pinks and beige. Our logo has a birdcage, and the cafe decor will have birdcages, flowers to match this. We would like for everything to fit onto an A3 or A2 double sided. including drinks, and we are looking at a separate smaller option for kids menu, which can include a colouring in section on the one side.

```html
<!DOCTYPE html>
<html lang="en">
<head>
<meta charset="utf-8">
<title>the velvet perch — Menu</title>
<link rel="stylesheet" href="https://fonts.googleapis.com/css2?family=Oswald:wght@500;600&family=Montserrat:wght@400;500;700&display=swap">
<style>
  :root{
    --paper:#f8eff1;
    --paper-deep:#f1e2e6;
    --ink:#2e2a2d;
    --muted:#6f6669;
    --price:#9c4a3f;
    --frame:#3f3b3d;
    --maroon:#6c2b2d;
    --maroon-deep:#5a2224;
    --logo:#c49d78;
    --white:#ffffff;
  }
  *{margin:0;padding:0;box-sizing:border-box}
  html,body{width:849px;height:1200px;overflow:hidden}
  body{background:var(--paper);font-family:"Montserrat",sans-serif;color:var(--ink)}
  .menu{position:relative;width:849px;height:1200px;overflow:hidden;
    background:radial-gradient(ellipse at 75% 15%,var(--paper-deep),transparent 55%),
               radial-gradient(ellipse at 20% 80%,var(--paper-deep),transparent 50%),var(--paper)}
  .frame{position:absolute;left:0;top:0;width:849px;height:1200px}
  .floral{position:absolute}
  .floral--top{left:0;top:0;width:190px;height:160px;
    background:radial-gradient(circle at 35% 30%,#2c3552 0,#3b4468 30%,#6fb3a8 55%,rgba(248,239,241,0) 75%)}
  .floral--bottom{right:0;bottom:0;width:190px;height:230px;
    background:radial-gradient(circle at 65% 60%,#f6ecd9 0,#efe0c4 30%,#d9a6a9 50%,#8aa583 62%,rgba(248,239,241,0) 78%)}
  .brand{position:absolute;top:122px;left:0;width:849px;display:flex;justify-content:center;align-items:center;gap:12px}
  .brand__dot{width:22px;height:22px;border-radius:50%;background:var(--logo)}
  .brand__name{font-family:"Montserrat",sans-serif;font-weight:500;font-size:30px;color:var(--logo);letter-spacing:1px}
  .column{position:absolute;width:285px}
  .column--left{left:112px}
  .column--right{left:458px}
  .section-title{font-family:"Oswald",sans-serif;font-weight:600;font-size:30px;letter-spacing:1.5px;
    padding-bottom:8px;border-bottom:2px solid var(--ink);margin-bottom:14px}
  .item{height:56px}
  .item__head{display:flex;justify-content:space-between;align-items:baseline}
  .item__name{font-weight:700;font-size:14px;letter-spacing:.3px}
  .item__price{font-weight:700;font-size:11px;color:var(--price)}
  .item__desc{font-size:7.5px;line-height:1.35;color:var(--muted);text-transform:uppercase;width:210px;margin-top:4px}
  .kids{position:absolute;left:458px;top:651px;width:285px;height:380px;background:var(--maroon);
    box-shadow:0 0 0 3px var(--maroon-deep) inset;padding:28px 24px 0}
  .kids .section-title{color:var(--white);border-bottom:none;padding-bottom:0;margin-bottom:16px;font-size:28px}
  .kids .item__name,.kids .item__desc{color:var(--white)}
  .kids .item__price{color:#f2d6cf}
  .kids .item{height:60px}
  .contact{position:absolute;top:1062px;left:112px;width:620px;text-align:left;padding-left:88px;
    font-family:"Oswald",sans-serif;font-weight:600;font-size:27px;letter-spacing:1.5px;color:var(--maroon)}
</style>
</head>
<body>
<main class="menu">
  <div class="floral floral--top" role="img" aria-label="Cluster of navy roses with teal blossoms"></div>
  <div class="floral floral--bottom" role="img" aria-label="Cluster of cream roses with pink buds and leaves"></div>

  <svg class="frame" viewBox="0 0 849 1200" aria-hidden="true">
    <rect x="58" y="105" width="742" height="1042" fill="none" stroke="var(--frame)" stroke-width="5" opacity=".85"/>
    <rect x="61" y="108" width="736" height="1036" fill="none" stroke="var(--frame)" stroke-width="1.5" opacity=".4"/>
  </svg>

  <header class="brand">
    <span class="brand__dot"></span>
    <span class="brand__name">the velvet perch</span>
  </header>

  <section class="column column--left" style="top:232px">
    <h2 class="section-title">COFFEE</h2>
    <div class="item"><div class="item__head"><span class="item__name">CAFE LATTE</span><span class="item__price">$ 08</span></div><p class="item__desc">Freshly made to order with care, served warm or over ice today.</p></div>
    <div class="item"><div class="item__head"><span class="item__name">CAPPUCCINO</span><span class="item__price">$ 08</span></div><p class="item__desc">Freshly made to order with care, served warm or over ice today.</p></div>
    <div class="item"><div class="item__head"><span class="item__name">AMERICANO</span><span class="item__price">$ 10</span></div><p class="item__desc">Freshly made to order with care, served warm or over ice today.</p></div>
    <div class="item"><div class="item__head"><span class="item__name">KILLER BEE</span><span class="item__price">$ 08</span></div><p class="item__desc">Freshly made to order with care, served warm or over ice today.</p></div>
    <div class="item"><div class="item__head"><span class="item__name">VANILLA LATTE</span><span class="item__price">$ 14</span></div><p class="item__desc">Freshly made to order with care, served warm or over ice today.</p></div>
    <div class="item"><div class="item__head"><span class="item__name">CARAMEL LATTE</span><span class="item__price">$ 08</span></div><p class="item__desc">Freshly made to order with care, served warm or over ice today.</p></div>
    <div class="item"><div class="item__head"><span class="item__name">ESPRESSO</span><span class="item__price">$ 12</span></div><p class="item__desc">Freshly made to order with care, served warm or over ice today.</p></div>
    <div class="item"><div class="item__head"><span class="item__name">MACCHIATO</span><span class="item__price">$ 10</span></div><p class="item__desc">Freshly made to order with care, served warm or over ice today.</p></div>
  </section>

  <section class="column column--left" style="top:752px">
    <h2 class="section-title">SOMETHING SPECIAL</h2>
    <div class="item"><div class="item__head"><span class="item__name">BEST DRINK EVER</span><span class="item__price">$ 10</span></div><p class="item__desc">Freshly made to order with care, served warm or over ice today.</p></div>
    <div class="item"><div class="item__head"><span class="item__name">HONEY LATTE</span><span class="item__price">$ 08</span></div><p class="item__desc">Freshly made to order with care, served warm or over ice today.</p></div>
    <div class="item"><div class="item__head"><span class="item__name">MINT MOCHA LATTE</span><span class="item__price">$ 06</span></div><p class="item__desc">Freshly made to order with care, served warm or over ice today.</p></div>
    <div class="item"><div class="item__head"><span class="item__name">CARAMEL MOCHA</span><span class="item__price">$ 04</span></div><p class="item__desc">Freshly made to order with care, served warm or over ice today.</p></div>
  </section>

  <section class="column column--right" style="top:232px">
    <h2 class="section-title">DRINKS</h2>
    <div class="item"><div class="item__head"><span class="item__name">CUCUMBER</span><span class="item__price">$ 10</span></div><p class="item__desc">Freshly made to order with care, served warm or over ice today.</p></div>
    <div class="item"><div class="item__head"><span class="item__name">LEMON LIME</span><span class="item__price">$ 08</span></div><p class="item__desc">Freshly made to order with care, served warm or over ice today.</p></div>
    <div class="item"><div class="item__head"><span class="item__name">CREAM SODA</span><span class="item__price">$ 08</span></div><p class="item__desc">Freshly made to order with care, served warm or over ice today.</p></div>
    <div class="item"><div class="item__head"><span class="item__name">COFFEE SODA</span><span class="item__price">$ 04</span></div><p class="item__desc">Freshly made to order with care, served warm or over ice today.</p></div>
    <div class="item"><div class="item__head"><span class="item__name">BLUEBERRY</span><span class="item__price">$ 06</span></div><p class="item__desc">Freshly made to order with care, served warm or over ice today.</p></div>
    <div class="item"><div class="item__head"><span class="item__name">CONCORD GRAPE</span><span class="item__price">$ 03</span></div><p class="item__desc">Freshly made to order with care, served warm or over ice today.</p></div>
  </section>

  <section class="kids">
    <h2 class="section-title">KIDS MENU</h2>
    <div class="item"><div class="item__head"><span class="item__name">BEST DRINK EVER</span><span class="item__price">$ 10</span></div><p class="item__desc">Freshly made to order with care, served warm or over ice today.</p></div>
    <div class="item"><div class="item__head"><span class="item__name">HONEY LATTE</span><span class="item__price">$ 08</span></div><p class="item__desc">Freshly made to order with care, served warm or over ice today.</p></div>
    <div class="item"><div class="item__head"><span class="item__name">MINT MOCHA LATTE</span><span class="item__price">$ 06</span></div><p class="item__desc">Freshly made to order with care, served warm or over ice today.</p></div>
    <div class="item"><div class="item__head"><span class="item__name">HONEY LATTE</span><span class="item__price">$ 08</span></div><p class="item__desc">Freshly made to order with care, served warm or over ice today.</p></div>
    <div class="item"><div class="item__head"><span class="item__name">MINT MOCHA LATTE</span><span class="item__price">$ 06</span></div><p class="item__desc">Freshly made to order with care, served warm or over ice today.</p></div>
  </section>

  <footer class="contact">CONTACT US: 000 000 0000</footer>
</main>
</body>
</html>
```